Upscale business cards needed for Board of Directors

We need professional business cards created for members of our family business Board of Directors. We would like these relatively simple and straightforward, but also with a unique element to set them apart. Probably stick with neutral and simple colors - white, grey etc. We need space for the traditional elements, including name, title, address, email/phone number. And we will be creating several from this template so it needs to be template that is easy to switch information in and out of.
Business
See description

```html
<!DOCTYPE html>
<html lang="en">
<head>
<meta charset="utf-8">
<title>Harbourline Holdings – Business Card</title>
<link href="https://fonts.googleapis.com/css2?family=Roboto:wght@300;400;700&display=swap" rel="stylesheet">
<style>
  :root {
    --page-bg: #e7e4df;
    --card-top: #f2f1ee;
    --band-dark-1: #161616;
    --band-dark-2: #2b2928;
    --gold-dark: #7d6240;
    --gold-light: #c8a46c;
    --gold-rule: #9c7d52;
    --gold-text: #b8935d;
    --ink: #1c1c1c;
    --light-text: #ebe9e5;
    --grey-text: #c4c4c4;
    --site-text: #efe6d6;
  }
  * { box-sizing: border-box; margin: 0; padding: 0; }
  html, body {
    width: 1200px;
    height: 969px;
    overflow: hidden;
    background: var(--page-bg);
    font-family: "Roboto", Arial, sans-serif;
  }
  .business-card {
    position: absolute;
    left: 100px;
    top: 198px;
    width: 1000px;
    height: 572px;
    background: var(--card-top);
    box-shadow: 0 18px 40px rgba(0,0,0,0.18);
    overflow: hidden;
  }
  .brand-rule {
    position: absolute;
    left: 58px;
    top: 84px;
    width: 426px;
    height: 6px;
    background: var(--gold-rule);
  }
  .brand-name {
    position: absolute;
    left: 58px;
    top: 112px;
    color: var(--ink);
    font-size: 40px;
    font-weight: 700;
    letter-spacing: 2px;
    line-height: 1;
    white-space: nowrap;
  }
  .info-band {
    position: absolute;
    left: 0;
    top: 280px;
    width: 100%;
    height: 236px;
    background: linear-gradient(90deg, var(--band-dark-1) 0%, var(--band-dark-2) 45%, var(--band-dark-1) 100%);
  }
  .person {
    position: absolute;
    left: 58px;
    top: 90px;
  }
  .person-name {
    color: var(--gold-text);
    font-size: 31px;
    font-weight: 400;
    letter-spacing: 1px;
  }
  .person-title {
    margin-top: 8px;
    color: var(--light-text);
    font-size: 25px;
    font-weight: 400;
    letter-spacing: 0.5px;
  }
  .contact {
    position: absolute;
    left: 651px;
    top: 44px;
    font-size: 24px;
    font-weight: 300;
    color: var(--grey-text);
    line-height: 34px;
    white-space: nowrap;
  }
  .contact-lines { margin-bottom: 18px; }
  .contact .label { color: var(--gold-text); }
  .contact .phone { color: var(--gold-text); }
  .web-band {
    position: absolute;
    left: 0;
    top: 516px;
    width: 100%;
    height: 56px;
    background: linear-gradient(90deg, var(--gold-dark) 0%, var(--gold-light) 40%, var(--gold-light) 60%, var(--gold-dark) 100%);
    display: flex;
    align-items: center;
    justify-content: center;
  }
  .website {
    color: var(--site-text);
    font-size: 23px;
    font-weight: 300;
    letter-spacing: 11px;
  }
</style>
</head>
<body>
  <main class="business-card">
    <div class="brand-rule"></div>
    <p class="brand-name">HARBOURLINE HOLDINGS</p>

    <section class="info-band">
      <div class="person">
        <p class="person-name">MARTIN HALE</p>
        <p class="person-title">PRESIDENT</p>
      </div>
      <div class="contact">
        <div class="contact-lines">
          <p>4127 Kingsbridge Lane</p>
          <p>Cedar Grove, NJ 07009</p>
        </div>
        <p class="phone"><span class="label">P :</span> 555 0148 3920</p>
        <p><span class="label">E :</span> martin@harbourline.com</p>
      </div>
    </section>

    <footer class="web-band">
      <span class="website">www.harbourline.com</span>
    </footer>
  </main>
</body>
</html>
```